High-end construction company needs a business card design

We need a modern looking business card that draws people in, is memorable and looks so good people will want to sick it on their fridges.
On the first side what is needed are:
Logo
My name - Tomasz Brelwik
Title - Managing Director
Website - www.varkelt.co.uk
Email - tomasz@varkelt.co.uk
Telephone - 020 5194 6281
Mobile - 07845139072
On the back side was is needed is a list of all the services we provide:
-Kitchen Renovations
-Bathroom Renovations
-House Renovations
-Garage Conversions
-Extensions
-Loft Conversions
-Conservatories
-Carpentry
-Tiling
-Electrical
-Plumbing & Heating
-Bricklaying
-Landscaping
-Decorating
-Plastering
We would like the colours to be the same shades as on the logo with grey or black for the words.
Target Market(s)
Anyone who needs building work done
Contact Information for Business Card
This business card is for a construction company which strives to deliver excellent service and quality.
The look and feel of the card should represent this.
Requirements
Must have
- On the first side what is needed are:
Logo
My name - Tomasz Brelwik
Title - Managing Director
Website - www.varkelt.co.uk
Email - tomasz@varkelt.co.uk
Telephone - 020 5194 6281
Mobile - 07845139072
Nice to have
- Cool looking features

```html
<!DOCTYPE html>
<html lang="en">
<head>
<meta charset="utf-8">
<title>Varkelt Construction Ltd – Business Card</title>
<link href="https://fonts.googleapis.com/css2?family=Exo+2:wght@400;600;700;800&display=swap" rel="stylesheet">
<style>
  :root {
    --backdrop: #8c8c8c;
    --paper: #ffffff;
    --green-dark: #4b8d40;
    --green-light: #6dbd45;
    --text-light: #ffffff;
  }
  * { margin: 0; padding: 0; box-sizing: border-box; }
  html, body {
    width: 1125px; height: 1200px; overflow: hidden;
    background: var(--backdrop);
    font-family: "Exo 2", Arial, sans-serif;
  }
  .card {
    position: absolute;
    left: 171px;
    width: 826px; height: 471px;
    overflow: hidden;
  }
  .card-front { top: 106px; background: var(--paper); }
  .card-back { top: 640px; background: var(--green-dark); color: var(--text-light); }

  .front-band { position: absolute; left: 0; top: 0; width: 826px; height: 471px; }

  .wordmark {
    position: absolute; left: 0; right: 0; top: 160px;
    text-align: center; color: var(--green-light); font-weight: 800;
  }
  .wordmark-name { display: block; font-size: 78px; line-height: 1; letter-spacing: 2px; }
  .wordmark-sub { display: block; font-size: 19px; letter-spacing: 3.5px; margin-top: 8px; }

  .contact-list {
    position: absolute; left: 45px; top: 344px;
    list-style: none; color: var(--text-light);
    font-size: 17.5px; line-height: 24px;
  }
  .contact-list li { display: flex; align-items: center; }
  .contact-icon { width: 16px; height: 16px; margin-right: 12px; fill: var(--text-light); }

  .person {
    position: absolute; right: 54px; top: 360px;
    text-align: right; color: var(--text-light);
  }
  .person-name { font-size: 27px; font-weight: 700; line-height: 1.1; }
  .person-title { font-size: 17px; }

  .back-wordmark {
    position: absolute; left: 0; right: 0; top: 196px;
    text-align: center; font-weight: 800; font-size: 54px; letter-spacing: 3px;
  }
  .back-rule {
    position: absolute; left: 141px; top: 279px; width: 518px; height: 3px;
    background: var(--text-light);
  }
  .services {
    position: absolute; left: 0; right: 0; top: 312px;
    text-align: center; font-size: 17.5px; line-height: 23.5px;
  }
  .tick { font-weight: 600; }
</style>
</head>
<body>

<section class="card card-front" aria-label="Front of business card">
  <svg class="front-band" viewBox="0 0 826 471" aria-hidden="true">
    <polygon fill="var(--green-dark)" points="0,313 640,313 673,346 706,313 826,313 826,471 0,471"/>
    <polyline fill="none" stroke="var(--green-light)" stroke-width="5" points="0,305 635,305 673,343 711,305 826,305"/>
    <rect x="667" y="303" width="11" height="11" fill="var(--green-light)"/>
  </svg>

  <div class="wordmark">
    <span class="wordmark-name">VARKELT</span>
    <span class="wordmark-sub">CONSTRUCTION LTD</span>
  </div>

  <ul class="contact-list">
    <li>
      <svg class="contact-icon" viewBox="0 0 16 16" aria-hidden="true"><path d="M3.5 1.5l2.5 0 1.2 3.2-1.7 1.3c.9 1.9 2.3 3.3 4.2 4.2l1.3-1.7 3.2 1.2v2.5c0 .9-.8 1.6-1.7 1.5C6.9 13.2 2.8 9.1 2 4.2 1.9 3.3 2.6 1.5 3.5 1.5z"/></svg>
      020 5194 6281
    </li>
    <li>
      <svg class="contact-icon" viewBox="0 0 16 16" aria-hidden="true"><path d="M4.5 0.5h7a1 1 0 0 1 1 1v13a1 1 0 0 1-1 1h-7a1 1 0 0 1-1-1v-13a1 1 0 0 1 1-1zm.6 2v9.5h5.8V2.5zM8 12.8a.9.9 0 1 0 0 1.8.9.9 0 0 0 0-1.8z"/></svg>
      07845139072
    </li>
    <li>
      <svg class="contact-icon" viewBox="0 0 16 16" aria-hidden="true"><path d="M1.5 4h13v8.5h-13zM2.5 5l5.5 4 5.5-4v.9L8 10 2.5 5.9z"/></svg>
      tomasz@varkelt.co.uk
    </li>
    <li>
      <svg class="contact-icon" viewBox="0 0 16 16" aria-hidden="true"><path d="M8 1a7 7 0 1 0 0 14A7 7 0 0 0 8 1zm-1 2.2c-.3.8-1.4 1-1.6 1.9.6.7 1.8.3 2.2 1.2-.4.9-1.6 1.2-1.5 2.3.4 1 1.3 1.6 1.2 2.8L7 12.9A5 5 0 0 1 7 3.2zm2.7.1a5 5 0 0 1 3.2 5.5c-.8-.3-1.5-1.2-2.4-.8-.7.4-.3 1.6-1 1.9-.7-.6-.6-1.9-1.5-2.3.4-.9 1.6-.7 2-1.6-.3-.8-1.2-1.4-.3-2.7z"/></svg>
      www.varkelt.co.uk
    </li>
  </ul>

  <div class="person">
    <div class="person-name">Tomasz Brelwik</div>
    <div class="person-title">Managing Director</div>
  </div>
</section>

<section class="card card-back" aria-label="Back of business card">
  <div class="back-wordmark">VARKELT</div>
  <div class="back-rule"></div>
  <p class="services">
    Kitchen Renovations <span class="tick">✓</span> Bathroom Renovations <span class="tick">✓</span> House Renovations<br>
    Garage Conversions <span class="tick">✓</span> Extensions <span class="tick">✓</span> Loft Conversions <span class="tick">✓</span> Conservatories<br>
    Carpentry <span class="tick">✓</span> Tiling <span class="tick">✓</span> Electrical <span class="tick">✓</span> Plumbing &amp; Heating <span class="tick">✓</span> Bricklaying<br>
    Landscaping <span class="tick">✓</span> Decorating <span class="tick">✓</span> Plastering
  </p>
</section>

</body>
</html>
```